Lunelle Rosa Hair Fancy Business Card’s

I want my business cards to be elite, original and very classy. I want the business cards to match the colors of my logo and to match the design posted. I would love the design of the picture I posted

I want the card all white .
The dripping on the top of the card I want it to match the pink color in my logo that’s also posted .
I need my logo on the business card !
I need my Instagram- @lunelle.rosa.hair__
And my phone number - 555 207 3962

Target Market(s)

My target market is young woman age 23 to older woman to the age of 65
I want both older and younger women to love my design . I don’t want any cheap looking business cards

Industry/Entity Type

Hair And Beauty

Contact Information for Business Card

Add my logo
Add my Instagram- @lunelle.rosa.hair__
My number - 555 207 3962
My website- www.lunellerosahair.example

Font styles to use
Serif
Script

Colors
ffffff
e667a6
e34298

Requirements
Must have
• The business cards must have my logo, my number , my website, and my Instagram!
Nice to have
• Nice to have glitter words that match my logo
• The business cards must look classy and mature
• I want them to be very unique!!
Should not have
• Should not have any colors that doesn’t match my logo ! This is very important! Please

```html
<!DOCTYPE html>
<html lang="en">
<head>
<meta charset="utf-8">
<title>Lunelle Rosa Hair – Business Card</title>
<link rel="stylesheet" href="https://fonts.googleapis.com/css2?family=Cinzel:wght@500&family=Poppins:wght@400;500&display=swap">
<style>
  :root {
    --stage: #161616;
    --card-white: #ffffff;
    --card-charcoal: #3f3f47;
    --pink: #e34298;
    --pink-soft: #e667a6;
    --ink: #4a4a4a;
    --muted: #7a7a7a;
    --silver-dark: #8c8c8c;
    --silver-light: #d9d9d9;
  }
  * { box-sizing: border-box; margin: 0; padding: 0; }
  html, body {
    width: 1125px; height: 1200px; overflow: hidden;
    background: var(--stage);
    font-family: "Poppins", sans-serif;
  }
  .card {
    position: absolute;
    left: 157px;
    width: 826px;
    height: 472px;
    overflow: hidden;
  }
  .card--front { top: 106px; background: var(--card-white); }
  .card--back { top: 639px; background: var(--card-charcoal); display: flex; align-items: center; justify-content: center; }

  .top-drip {
    position: absolute; left: 0; top: 0; width: 826px; height: 56px;
  }
  .top-drip path { fill: var(--pink); }

  .brand-name {
    font-family: "Poppins", sans-serif;
    font-weight: 500;
    letter-spacing: 1px;
    white-space: nowrap;
  }
  .card--front .brand-name {
    position: absolute; left: 40px; top: 130px;
    font-size: 36px; color: var(--pink);
  }
  .card--back .brand-name {
    font-size: 50px; color: var(--card-white);
  }

  .contact-list {
    position: absolute; left: 40px; top: 330px;
    list-style: none;
  }
  .contact-item {
    display: flex; align-items: center; gap: 10px;
    font-size: 18.5px; line-height: 24px; color: var(--ink);
  }
  .contact-icon { width: 15px; height: 15px; flex: none; fill: var(--pink); }

  .holder {
    position: absolute; right: 49px; top: 352px; text-align: right;
  }
  .holder-name {
    font-family: "Cinzel", serif; font-weight: 500;
    font-size: 26px; letter-spacing: 1px; color: var(--pink); line-height: 1.1;
  }
  .holder-role {
    font-size: 18px; color: var(--muted); margin-top: 2px;
  }

  .footer-band {
    position: absolute; left: 0; bottom: 0; width: 100%; height: 21px;
    display: flex; gap: 3px;
  }
  .footer-band-pink { width: 502px; background: var(--pink); }
  .footer-band-silver {
    flex: 1;
    background: linear-gradient(90deg, var(--silver-dark), var(--silver-light) 35%, var(--silver-dark) 65%, var(--silver-light));
  }
</style>
</head>
<body>
  <section class="card card--front">
    <svg class="top-drip" viewBox="0 0 826 56" preserveAspectRatio="none" aria-hidden="true">
      <path d="M0 0H826V14
               C800 14 792 16 790 24 C788 34 786 40 780 40 C774 40 772 34 771 24 C770 16 760 14 730 14
               C690 14 684 16 682 30 C680 46 676 52 670 52 C664 52 661 46 660 30 C659 16 650 14 610 14
               C560 14 556 16 554 22 C552 30 550 34 545 34 C540 34 538 30 537 22 C536 16 520 14 470 14
               C420 14 414 16 412 28 C410 40 406 46 400 46 C394 46 391 40 390 28 C389 16 380 14 330 14
               C280 14 274 16 272 24 C270 32 268 36 263 36 C258 36 256 32 255 24 C254 16 240 14 190 14
               C140 14 134 16 132 30 C130 44 126 50 120 50 C114 50 111 44 110 30 C109 16 100 14 60 14
               C40 14 36 16 35 22 C34 28 32 31 28 31 C24 31 22 28 21 22 C20 16 12 14 0 14Z"/>
    </svg>

    <div class="brand-name">Lunelle Rosa Hair</div>

    <ul class="contact-list">
      <li class="contact-item">
        <svg class="contact-icon" viewBox="0 0 24 24"><path d="M6.6 10.8a15.1 15.1 0 0 0 6.6 6.6l2.2-2.2a1 1 0 0 1 1-.25 11.4 11.4 0 0 0 3.6.57 1 1 0 0 1 1 1V20a1 1 0 0 1-1 1A17 17 0 0 1 3 4a1 1 0 0 1 1-1h3.5a1 1 0 0 1 1 1c0 1.25.2 2.45.57 3.57a1 1 0 0 1-.25 1z"/></svg>
        555 207 3962
      </li>
      <li class="contact-item">
        <svg class="contact-icon" viewBox="0 0 24 24"><rect x="4" y="4" width="16" height="16" rx="2"/></svg>
        @lunelle.rosa.hair__
      </li>
      <li class="contact-item">
        <svg class="contact-icon" viewBox="0 0 24 24"><path d="M3 6h18v12H3z M3 6l9 7 9-7" fill="var(--pink)" stroke="#fff" stroke-width="1.5"/></svg>
        info@lunellerosahair.example
      </li>
      <li class="contact-item">
        <svg class="contact-icon" viewBox="0 0 24 24"><circle cx="12" cy="12" r="10"/><path d="M2 12h20M12 2c3 3 3 17 0 20M12 2c-3 3-3 17 0 20" fill="none" stroke="#fff" stroke-width="1.4"/></svg>
        www.lunellerosahair.example
      </li>
    </ul>

    <div class="holder">
      <div class="holder-name">Dorian Vale</div>
      <div class="holder-role">President</div>
    </div>

    <div class="footer-band">
      <div class="footer-band-pink"></div>
      <div class="footer-band-silver" role="img" aria-label="Silver glitter texture strip"></div>
    </div>
  </section>

  <section class="card card--back">
    <div class="brand-name">Lunelle Rosa Hair</div>
  </section>
</body>
</html>
```